Consulting Company PowerPoint Template Design

We are looking for an updated PowerPoint template design or our 55 person energy consulting firm (K7) based in San Francisco (www.kseven-example.com). We would like two versions of the same PowerPoint template in a 16:9 and 4:3 format with our existing logo.

We have an existing color scheme and template and are seeking your help to polish/update the template design for wide format and create a flexible template that is easy to use with content from Excel and Word. Our current template, and a couple of examples that we like are attached.

Specific requests include:

• Dark background for slide title
• A narrow section header
• Maximizing white space for content
• A limited number of well designed Master template layouts to choose from
• A selection of title and section header slides that are not San Francisco specific with some variety to chose from ideally with a focus on energy or nature, graphics/visuals.

For examples of energy specific templates see:
https://www.brightslidehub.example/energy/powerpoint-templates/0.html

Requirements
Must have
• Must use our logo but open to other designs, fonts, and styles for the PowerPoint template.
• Please use our existing color scheme found in the attached Excel file.
• Also we would like the ability to easily copy and paste from our existing/original template to the new template. In other words we would like backward compatibility to apply the new template format to our old PowerPoints that use our existing template.

```html
<!DOCTYPE html>
<html lang="en">
<head>
<meta charset="utf-8">
<title>K7 Slide Template – Bullet Layout</title>
<link rel="stylesheet" href="https://fonts.googleapis.com/css2?family=Titillium+Web:wght@400;600;700&display=swap">
<style>
  :root {
    --navy: #0b4a6e;
    --gold: #d8b36c;
    --white: #ffffff;
    --body-grey: #8c8c8c;
    --ring: #dfe6ea;
  }
  * { margin: 0; padding: 0; box-sizing: border-box; }
  html, body {
    width: 1200px; height: 900px; overflow: hidden;
    background: var(--white);
    font-family: "Titillium Web", sans-serif;
  }
  .slide { position: relative; width: 1200px; height: 900px; overflow: hidden; background: var(--white); }

  .title-bar { position: absolute; left: 0; top: 0; width: 1200px; height: 76px; }
  .title-bar svg { position: absolute; left: 0; top: 0; }
  .slide-title {
    position: absolute; left: 18px; top: 9px;
    font-size: 31px; font-weight: 600; letter-spacing: 0.5px;
    color: var(--white); line-height: 48px;
  }
  .slide-title .accent { color: var(--gold); }

  .brand-badge {
    position: absolute; width: 78px; height: 78px; border-radius: 50%;
    background: var(--navy); border: 4px solid var(--white);
    box-shadow: 0 0 0 2px var(--ring);
    display: flex; align-items: center; justify-content: center;
    color: var(--white); font-weight: 700; font-size: 28px; line-height: 1;
  }
  .brand-badge.header { left: 1110px; top: 6px; }

  .bullet-list { position: absolute; left: 0; top: 0; width: 1200px; }
  .bullet { position: absolute; left: 0; width: 1200px; }
  .bullet .brand-badge { left: 43px; top: 0; width: 70px; height: 70px; font-size: 25px; }
  .bullet-title {
    position: absolute; left: 138px; top: 12px;
    font-size: 31px; font-weight: 700; color: var(--navy);
    letter-spacing: 0.6px; line-height: 40px; white-space: nowrap;
  }
  .bullet-text {
    position: absolute; left: 139px; top: 54px; width: 1000px;
    font-size: 19.5px; line-height: 28.5px; color: var(--body-grey);
    white-space: nowrap;
  }

  .footer { position: absolute; left: 0; top: 855px; width: 1200px; height: 45px; }
  .footer svg { position: absolute; left: 0; top: 0; }
  .company-name {
    position: absolute; left: 9px; top: 3px;
    font-size: 24px; font-weight: 700; color: var(--white); line-height: 40px;
  }
  .page-number {
    position: absolute; left: 1133px; top: 7px;
    font-size: 19px; font-weight: 600; color: var(--white); line-height: 36px;
  }
</style>
</head>
<body>
<div class="slide">

  <header class="title-bar">
    <svg width="1200" height="76" viewBox="0 0 1200 76" aria-hidden="true">
      <polygon points="0,66 1105,66 1118,76 0,76" fill="var(--gold)"/>
      <rect x="0" y="0" width="1200" height="66" fill="var(--navy)"/>
    </svg>
    <h1 class="slide-title"><span class="accent">PROJECT</span> TITLE HERE</h1>
    <div class="brand-badge header">K7</div>
  </header>

  <main class="bullet-list">
    <section class="bullet" style="top:146px">
      <div class="brand-badge">K7</div>
      <h2 class="bullet-title">BULLET TEXT TITLE HERE</h2>
      <p class="bullet-text">There are many variations of passages of Lorem Ipsum available, but the majority have suffered alteration in<br>some form, by injected humour, or randomised words which don’t look even slightly believable. It is a long estab-<br>lished fact that a reader will be distracted by the readable content of a page when looking at its layout.</p>
    </section>
    <section class="bullet" style="top:343px">
      <div class="brand-badge">K7</div>
      <h2 class="bullet-title">BULLET TEXT TITLE HERE</h2>
      <p class="bullet-text">There are many variations of passages of Lorem Ipsum available, but the majority have suffered alteration in<br>some form, by injected humour, or randomised words which don’t look even slightly believable. It is a long estab-<br>lished fact that a reader will be distracted by the readable content of a page when looking at its layout.</p>
    </section>
    <section class="bullet" style="top:540px">
      <div class="brand-badge">K7</div>
      <h2 class="bullet-title">BULLET TEXT TITLE HERE</h2>
      <p class="bullet-text">There are many variations of passages of Lorem Ipsum available, but the majority have suffered alteration in<br>some form, by injected humour, or randomised words which don’t look even slightly believable. It is a long estab-<br>lished fact that a reader will be distracted by the readable content of a page when looking at its layout.</p>
    </section>
  </main>

  <footer class="footer">
    <svg width="1200" height="45" viewBox="0 0 1200 45" aria-hidden="true">
      <rect x="0" y="0" width="1200" height="45" fill="var(--navy)"/>
      <polygon points="1102,3 1200,3 1200,45 1112,45 1092,22" fill="var(--gold)"/>
    </svg>
    <div class="company-name">Kestrel+Valley Economics</div>
    <div class="page-number">01</div>
  </footer>

</div>
</body>
</html>
```